Boutique custom software development company needs new business card

Our nearly 20 year old custom software development company would like to better include the fact that we are now providing Bitcoin services. These new services are B2B include education (how to acquire and securely hold Bitcoin) and integrating Bitcoin payments into existing ecommerce sites or other existing systems. Please keep the card clean and simple. Attached is our current design and some other files. vextorial.com

Target Market(s)

businesses owners interested in long term relationship

Industry/Entity Type

Custom software development and Bitcoin

Contact Information for Business Card

Dale Parker, dale@vextorial.com, vextorial.com, (888) 555-VXTRL

Font styles to use
Other font styles liked:
• monospace

Requirements
Must have
• double-sided
Nice to have
• clean and simple
Should not have
• physical address

```html
<!DOCTYPE html>
<html lang="en">
<head>
<meta charset="utf-8">
<title>Vextorial Business Card</title>
<link href="https://fonts.googleapis.com/css2?family=Open+Sans:wght@400;700&family=Lato:wght@400&display=swap" rel="stylesheet">
<style>
  :root {
    --brand-blue: #3d75b9;
    --brand-orange: #f07f25;
    --ink: #111111;
    --paper: #ffffff;
    --backdrop: #000000;
  }
  * { margin: 0; padding: 0; box-sizing: border-box; }
  html, body {
    width: 1200px; height: 1200px; overflow: hidden;
    background: var(--backdrop);
  }
  .canvas { position: relative; width: 1200px; height: 1200px; }

  .card {
    position: absolute; left: 218px; width: 756px; height: 431px;
    border-radius: 37px; overflow: hidden;
  }
  .card--front { top: 142px; background: var(--brand-blue); }
  .card--back { top: 619px; background: var(--paper); }

  .front-wordmark {
    position: absolute; left: 0; right: 0; top: 118px;
    text-align: center;
    font-family: "Open Sans", sans-serif; font-weight: 700;
    font-size: 94px; line-height: 1; letter-spacing: 1px;
    color: var(--paper);
  }
  .front-tagline {
    position: absolute; left: 0; right: 0; top: 250px;
    text-align: center;
    font-family: "Lato", sans-serif; font-weight: 400;
    font-size: 38px; letter-spacing: -1.6px; line-height: 1;
    color: var(--paper);
  }

  .brand-block {
    position: absolute; left: 99px; top: 121px; width: 190px; height: 190px;
    display: flex; flex-direction: column; align-items: center; justify-content: center; gap: 14px;
  }
  .brand-block__square { width: 110px; height: 110px; background: var(--brand-blue); }
  .brand-block__name {
    font-family: "Open Sans", sans-serif; font-weight: 700;
    font-size: 27px; letter-spacing: 1px; color: var(--brand-blue);
  }

  .divider {
    position: absolute; left: 376px; top: 103px; width: 1.5px; height: 224px;
    background: var(--brand-blue);
  }

  .contact { position: absolute; left: 432px; top: 118px; font-family: "Open Sans", sans-serif; color: var(--ink); }
  .contact__name { font-weight: 700; font-size: 32px; line-height: 1.1; letter-spacing: 0.3px; white-space: nowrap; }
  .contact__first { color: var(--brand-orange); }
  .contact__last { color: var(--brand-blue); }
  .contact__services { margin-top: 6px; font-size: 21px; line-height: 26px; white-space: nowrap; }
  .contact__list { list-style: none; margin-top: 12px; }
  .contact__item { display: flex; align-items: center; font-size: 21px; line-height: 25.5px; white-space: nowrap; }
  .contact__icon { width: 18px; height: 18px; margin-right: 11px; flex: none; }

  .footer-bands { position: absolute; left: 0; bottom: 0; width: 756px; height: 27px; }
</style>
</head>
<body>
<div class="canvas">

  <section class="card card--front">
    <div class="front-wordmark">VEXTORIAL</div>
    <div class="front-tagline">developer of custom applications</div>
  </section>

  <section class="card card--back">
    <div class="brand-block">
      <div class="brand-block__square"></div>
      <div class="brand-block__name">VEXTORIAL</div>
    </div>

    <div class="divider"></div>

    <div class="contact">
      <div class="contact__name"><span class="contact__first">Dale</span> <span class="contact__last">Parker</span></div>
      <div class="contact__services">Custom Software Development<br>Bitcoin Education &amp; Payments</div>
      <ul class="contact__list">
        <li class="contact__item">
          <svg class="contact__icon" viewBox="0 0 24 24" aria-hidden="true"><path fill="#f07f25" d="M6.6 10.8a15.1 15.1 0 0 0 6.6 6.6l2.2-2.2c.3-.3.7-.4 1-.2 1.1.4 2.3.6 3.6.6.6 0 1 .4 1 1V20c0 .6-.4 1-1 1C10.6 21 3 13.4 3 4c0-.6.4-1 1-1h3.5c.6 0 1 .4 1 1 0 1.3.2 2.5.6 3.6.1.3 0 .7-.2 1z"/><path fill="none" stroke="#f07f25" stroke-width="1.6" d="M14 3a7 7 0 0 1 7 7M14 6.5a3.5 3.5 0 0 1 3.5 3.5"/></svg>
          (888) 555-VXTRL
        </li>
        <li class="contact__item">
          <svg class="contact__icon" viewBox="0 0 24 24" aria-hidden="true"><circle cx="12" cy="12" r="10" fill="#f07f25"/><path fill="#fff" d="M7 6c2 0 3 1 3 2.5S8 10 8 12s2 2 2 4-1 3-2 3c-2-1-4-4-4-7 0-2 1-4 3-6zm8-2c2 1 4 3 5 5-2 0-3 1-4 0s-2-2-1-5zm1 9c2 0 3 1 3 2-1 2-3 4-5 4 0-2 0-6 2-6z"/></svg>
          www.vextorial.com
        </li>
        <li class="contact__item">
          <svg class="contact__icon" viewBox="0 0 24 24" aria-hidden="true"><path fill="#f07f25" d="M2 10l10-7 10 7v11H2z"/><path fill="#fff" d="M5 9h14v6l-7 4-7-4z"/><circle cx="12" cy="12" r="2.6" fill="none" stroke="#f07f25" stroke-width="1.3"/><path fill="#f07f25" d="M2 21l8-6h4l8 6z"/></svg>
          dale@vextorial.com
        </li>
      </ul>
    </div>

    <svg class="footer-bands" viewBox="0 0 756 27" preserveAspectRatio="none" aria-hidden="true">
      <polygon points="0,0 336,0 377,27 0,27" fill="var(--brand-orange)"/>
      <polygon points="365,0 756,0 756,27 405,27" fill="var(--brand-blue)"/>
    </svg>
  </section>

</div>
</body>
</html>
```